Norvane Website Design (New Start Up Investment Management Firm)

We need a website designed. We have attached a Powerpoint with our proposed website content (which is quite minimal), the format is just a suggestion but we would like to see your alternative and improved ideas. We are a boutique investment firm so are looking for something sleek and professional. I have included on the last page of the attachment our brand colours and font styles as well as attaching our logo design. We would like the successful designer to design the website and build the buttons etc.

On the "Contact Us" page, we are open to suggestions on how best to show the map, whether is should be static or open a google maps page. We would like the phone number and email address to be set up so people can click on them on their phone and it calls us or emails us directly.

We would prefer not to have photos of landscapes on the site.
Our website is hosted on a Linux based website.

We would also like 3 links at the bottom of each page for links to pdfs:
- Disclaimer, Terms and Conditions of Web Site Use
- Stewardship
- Pillar III

Target Market(s)

Institutional Investors

Industry/Entity Type

Investment

Coding

Coded - Design and coding required

Number of Pages Required

3 page

Font styles to use
Other font styles liked:
• Logo: Lato, Text: Source Sans Pro

Colors

Designer to choose colors to be used in the design.

Requirements
Must have
• The website must use the colours and fonts on the last page of the attached powerpoint. I can't see an option to select the exact colour palette below so please look at the PPT.
• For others please see Project description.
Should not have
• Landscape photos

```html
<!DOCTYPE html>
<html lang="en">
<head>
<meta charset="utf-8">
<title>Norvane Investment Management – Approach</title>
<link href="https://fonts.googleapis.com/css2?family=Lato:wght@300;400;700&display=swap" rel="stylesheet">
<style>
  :root {
    --navy: #0b2c5c;
    --footer: #002d62;
    --accent: #3f87d4;
    --accent-light: #5fa3e0;
    --body-text: #4a4f57;
    --white: #ffffff;
  }
  * { box-sizing: border-box; margin: 0; padding: 0; }
  html, body { width: 1200px; height: 796px; overflow: hidden; }
  body { font-family: "Lato", Arial, sans-serif; color: var(--body-text); position: relative; background: var(--white); }

  .hero-backdrop {
    position: absolute; left: 0; top: 0; width: 1200px; height: 674px;
    background:
      radial-gradient(ellipse 420px 260px at 1000px 300px, rgba(120,190,215,0.55), transparent 70%),
      radial-gradient(ellipse 360px 220px at 200px 560px, rgba(150,200,230,0.45), transparent 70%),
      radial-gradient(ellipse 300px 200px at 150px 250px, rgba(240,200,200,0.35), transparent 70%),
      linear-gradient(100deg, #f4f6f9 0%, #eaf1f6 45%, #d3e8f0 75%, #bcdde9 100%);
  }

  .site-header { position: absolute; left: 0; top: 0; width: 1200px; height: 110px; }
  .brand { position: absolute; left: 120px; top: 29px; display: flex; align-items: center; gap: 14px; }
  .brand-square { width: 48px; height: 48px; background: var(--navy); }
  .brand-text { display: flex; flex-direction: column; }
  .brand-name { font-size: 44px; font-weight: 400; color: var(--navy); line-height: 1; letter-spacing: 1px; }
  .brand-tagline { font-size: 8.5px; letter-spacing: 1.6px; color: var(--navy); margin-top: 4px; }

  .main-nav { position: absolute; top: 48px; left: 617px; display: flex; gap: 0; }
  .main-nav a { font-size: 16.5px; font-weight: 400; color: var(--navy); text-decoration: none; position: absolute; white-space: nowrap; }
  .main-nav a.is-active { color: var(--accent-light); }

  .page-title { position: absolute; top: 174px; left: 0; width: 1200px; text-align: center; font-size: 33px; font-weight: 400; color: var(--accent); letter-spacing: 0.5px; }

  .pillar { position: absolute; text-align: center; }
  .pillar-philosophy { left: 118px; top: 290px; width: 464px; }
  .pillar-approach { left: 617px; top: 287px; width: 468px; }
  .pillar-icon { display: block; margin: 0 auto; }
  .pillar h2 { font-size: 30px; font-weight: 400; color: var(--navy); margin-top: 12px; }
  .pillar p { font-size: 14.2px; font-weight: 300; line-height: 23px; color: var(--body-text); margin-top: 16px; }
  .pillar-approach p { margin-top: 21px; }

  .site-footer { position: absolute; left: 0; top: 674px; width: 1200px; height: 122px; background: var(--footer); color: var(--white); }
  .footer-links { position: absolute; left: 123px; top: 28px; font-size: 16.5px; font-weight: 400; }
  .footer-links a { color: var(--white); text-decoration: none; }
  .footer-links .sep { margin: 0 9px; }
  .copyright { position: absolute; left: 123px; top: 64px; font-size: 13px; font-weight: 300; }
  .social { position: absolute; left: 886px; top: 706px; display: flex; gap: 5px; }
  .social span { display: block; width: 36px; height: 36px; border: 1.5px solid var(--white); border-radius: 50%; }
</style>
</head>
<body>
  <div class="hero-backdrop" role="img" aria-label="Softly blurred background of financial market charts and coin stacks in pale blue tones"></div>

  <header class="site-header">
    <div class="brand">
      <div class="brand-square"></div>
      <div class="brand-text">
        <span class="brand-name">NORVANE</span>
        <span class="brand-tagline">INVESTMENT MANAGEMENT</span>
      </div>
    </div>
    <nav class="main-nav">
      <a href="#" style="left:0">HOME</a>
      <a href="#" style="left:94px">ABOUT US</a>
      <a href="#" class="is-active" style="left:218px">APPROACH</a>
      <a href="#" style="left:351px">CONTACT US</a>
    </nav>
  </header>

  <h1 class="page-title">OUR APPROACH AND PHILOSOPHY</h1>

  <section class="pillar pillar-philosophy">
    <svg class="pillar-icon" width="72" height="66" viewBox="0 0 72 66" fill="none" stroke="#3f87d4" stroke-width="4" stroke-linejoin="round">
      <path d="M4 14 H20 a7 7 0 1 1 14 0 H50 V28 a7 7 0 1 1 0 14 V58 H36 a7 7 0 1 0 -14 0 H10 V42 a7 7 0 1 1 0 -14 V14 Z"/>
    </svg>
    <h2>Philosophy</h2>
    <p>Norvane’s philosophy is based on the understanding that financial markets tend to mean revert and that valuations and fundamentals matter. Norvane strives to construct a resilient portfolio diversified across asset classes, strategies and time horizons to achieve our target return objective. Freedom of idea expression enables us to react nimbly to market dislocations</p>
  </section>

  <section class="pillar pillar-approach">
    <svg class="pillar-icon" width="84" height="84" viewBox="0 0 84 84" fill="none" stroke="#3f87d4" stroke-width="2.6" stroke-linecap="round">
      <circle cx="42" cy="42" r="5" fill="#3f87d4" stroke="none"/>
      <circle cx="42" cy="42" r="27" stroke-dasharray="14 7"/>
      <path d="M42 2 V30 M36 24 L42 30 L48 24"/>
      <path d="M42 82 V54 M36 60 L42 54 L48 60"/>
      <path d="M2 42 H30 M24 36 L30 42 L24 48"/>
      <path d="M82 42 H54 M60 36 L54 42 L60 48"/>
      <path d="M14 14 L32 32 M24 32 H32 V24"/>
      <path d="M70 14 L52 32 M60 32 H52 V24"/>
      <path d="M14 70 L32 52 M24 52 H32 V60"/>
      <path d="M70 70 L52 52 M60 52 H52 V60"/>
    </svg>
    <h2>Approach</h2>
    <p>Norvane combines asset allocation, macro trading, hedging and fund selection capabilities in an actively risk-managed portfolio. This model provides increased control, flexibility and liquidity while lowering the overall fee burden. Our risk posture and asset allocation are synchronised with our cycle and valuation frameworks. Bottom-up ideas are consistent with these top-down views. We look to protect against steep drawdowns in times of market stress, so that we are in a position to invest when risk premia and margins of safety are high</p>
  </section>

  <footer class="site-footer">
    <div class="footer-links">
      <a href="#">Disclaimer</a><span class="sep">|</span><a href="#">Terms and Conditions</a><span class="sep">|</span><a href="#">Stewardship</a><span class="sep">|</span><a href="#">Pillar III</a>
    </div>
    <div class="copyright">© 2017 Company Name&nbsp; All right reserved&nbsp; Term of Use</div>
  </footer>
  <div class="social" aria-label="Social media links">
    <span></span><span></span><span></span><span></span><span></span>
  </div>
</body>
</html>
```